BOLD & MINIMALIST DESIGN NEEDED

We want a very bold but minimalistic business card design that is impactful and utilizes both sides of the business card. Our current logo is included for your use.

We want bold fonts and good use of negative space. We don't want the logo to overpower the design.

Target Market(s)

Professionals who are building new commercial buildings.

Industry/Entity Type

Construction

Contact Information for Business Card

Name, Title, email, office phone, cell phone, website

Font styles to use
Serif
Sans Serif

Requirements
Must have
• Bold design!

```html
<!DOCTYPE html>
<html lang="en">
<head>
<meta charset="UTF-8">
<title>Summitline Works — Business Card</title>
<link href="https://fonts.googleapis.com/css2?family=Roboto:wght@700&display=swap" rel="stylesheet">
<style>
  :root {
    --backdrop: #dfe4e2;
    --card: #ffffff;
    --ink: #2a2a2a;
    --text: #555555;
    --rule: #222222;
  }
  * { margin: 0; padding: 0; box-sizing: border-box; }
  html, body {
    width: 1200px;
    height: 716px;
    overflow: hidden;
    background: var(--backdrop);
    font-family: "Roboto", Arial, sans-serif;
  }
  .canvas { position: relative; width: 1200px; height: 716px; }
  .card {
    position: absolute;
    left: 370px;
    width: 460px;
    height: 264px;
    background: var(--card);
    border-radius: 14px;
  }
  .card--front { top: 94px; }
  .card--back { top: 382px; }

  .wordmark {
    position: absolute;
    display: flex;
    align-items: center;
    justify-content: center;
    color: var(--ink);
    font-weight: 700;
    white-space: nowrap;
  }
  .wordmark__dot { border-radius: 50%; background: var(--ink); flex: none; }
  .wordmark__name { line-height: 1; }

  .card--front .wordmark { left: 0; right: 0; top: 106px; gap: 12px; }
  .card--front .wordmark__dot { width: 22px; height: 22px; }
  .card--front .wordmark__name { font-size: 34px; }

  .card--back .wordmark { left: 240px; width: 200px; top: 120px; gap: 8px; }
  .card--back .wordmark__dot { width: 13px; height: 13px; }
  .card--back .wordmark__name { font-size: 19px; }

  .contact {
    position: absolute;
    left: 16px;
    top: 58px;
    color: var(--text);
    font-weight: 700;
    font-size: 12.5px;
    line-height: 16.5px;
  }
  .contact__name { font-size: 15px; line-height: 18px; }
  .contact__title { font-size: 12px; margin-bottom: 18px; }
  .contact__address { margin-bottom: 17px; }
  .divider {
    position: absolute;
    left: 230px;
    top: 60px;
    width: 1px;
    height: 143px;
    background: var(--rule);
  }
</style>
</head>
<body>
<main class="canvas">
  <section class="card card--front" aria-label="Card front">
    <div class="wordmark">
      <span class="wordmark__dot"></span>
      <span class="wordmark__name">SUMMITLINE WORKS</span>
    </div>
  </section>

  <section class="card card--back" aria-label="Card back">
    <div class="contact">
      <p class="contact__name">CORIN VALE</p>
      <p class="contact__title">Designer</p>
      <p class="contact__address">Your Address Here<br>Unit 12 Harbor Row 7710</p>
      <p>+555-01-24680<br>hello@summitline.test<br>www.summitline.test</p>
    </div>
    <span class="divider"></span>
    <div class="wordmark">
      <span class="wordmark__dot"></span>
      <span class="wordmark__name">SUMMITLINE WORKS</span>
    </div>
  </section>
</main>
</body>
</html>
```